Mortgage Protection Insurance Flyer

The target audience are new home owners so the design needs to be clean and simple.

This a primarily for Final Expense Insurance, but need an area where it says "We Also Specialize In:"
- Medicare Supplement Insurance (MediGap)
- Annuities
- Final Expense

All flyer versions need to be editable. Colors to be used are red, white or black. Refer to my website for colors and photos (corvantshield.com). Will attach my logo and a flyer that I found online that is the format that I am looking for (for 8.5 in. x 11 in version). Need flyer in standard letter size 8.5 in. x11 in. but also in 8.5 in. x 5.5 in and 5.0 in. x 8.0 in. All sizes to be portrait oriented. If picked as winning design, need all flyer versions in full color, also in grey scale and files in all industry file types.

Content can be taken from my website..... corvantshield.com

Do NOT submit if you are not willing to provide all versions as described above for the original project price.

Must use royalty-free stock photos please.

Target Market(s)

New homeowners looking for insurance to protect there mortgage payments

Industry/Entity Type

Life Insurance

Colors
f69fa3

Requirements
Must have
• Colors to be used are red, white or black.
• Need flyer in standard letter size 8.5 in. x11 in. but also in 3.5 in. x 8.5 in (Full Bleed 3.75 in by 8.75 in.) and 4.0 in. x 6.0 in. (Full Bleed 4.12 in x 6.12 in) Each design tailored to the size dimensions (So no squeezing 8.5 x 11 design into a 4.0 x 6.0 space.) All sizes to be portrait oriented. If picked as winning design, need all flyer versions in full color, also in grey scale and files in all file types.
• Do not need physical address on flyer, do need email address on flyer though - tkelwer@corvantshield.com
• So phone number should be prominent, email address and website address should also be contact area.
• If you can not agree to terms above, do not submit any designs.
• Need facebook & twitter logos somewhere in contact info area.
Nice to have
• See sample flyers I have attached.
• White background with red used as primary graphic color and black used as secondary graphic if needed.
• font to be used should similar to one used in logo.

```html
<!DOCTYPE html>
<html lang="en">
<head>
<meta charset="utf-8">
<title>Corvant Shield Insurance – Flyer</title>
<link rel="stylesheet" href="https://fonts.googleapis.com/css2?family=Montserrat:wght@400;500;600;700;800&family=Roboto+Condensed:ital,wght@1,800&family=Open+Sans:wght@600;700&display=swap">
<style>
:root{
  --red:#d8222a;
  --ink:#1f1f1f;
  --text:#3a3a3a;
  --paper:#efefef;
  --paper-light:#f5f5f5;
  --chip:#dcdcdc;
  --footer-dark:#262626;
  --stage:#4a4a4a;
  --white:#ffffff;
}
*{box-sizing:border-box;margin:0;padding:0}
html,body{width:1200px;height:857px;overflow:hidden}
body{background:var(--stage);font-family:"Montserrat",sans-serif;color:var(--text)}
.flyer{position:absolute;left:295px;top:20px;width:609px;height:817px;background:linear-gradient(180deg,var(--paper-light),var(--paper));overflow:hidden}
.hero-photo{position:absolute;left:290px;top:0;width:290px;height:302px;z-index:0;background:linear-gradient(90deg,rgba(239,239,239,0) 0%,#dcdcdc 25%,#c9c9cb 55%,#b9babd 80%,#d8d8d8 100%)}
.brand{position:absolute;left:29px;top:42px;z-index:1;display:flex;align-items:center;gap:9px;width:250px}
.brand-mark{flex:0 0 14px;height:14px;background:var(--red)}
.brand-name{font-family:"Montserrat",sans-serif;font-weight:800;font-size:21px;line-height:21px;letter-spacing:.3px;color:var(--ink)}
.headline{position:absolute;left:29px;top:152px;z-index:1;width:258px;font-family:"Roboto Condensed",sans-serif;font-style:italic;font-weight:800;font-size:37px;line-height:44px;color:var(--ink);text-transform:uppercase;letter-spacing:-.6px;white-space:nowrap}
.headline .accent{color:var(--red)}
.hero-rule{position:absolute;left:29px;top:308px;width:551px;height:4px;background:var(--red)}
.col{position:absolute;font-size:9.6px;line-height:12.4px}
.col-left{left:29px;top:333px;width:255px}
.col-right{left:324px;top:333px;width:256px}
.intro,.para{text-align:justify}
.heading{font-weight:700;color:var(--red);font-size:12px;line-height:14px;margin-bottom:5px}
.ticks{list-style:none}
.ticks li{position:relative;padding-left:13px;margin-bottom:6px}
.ticks li svg{position:absolute;left:0;top:2px;width:8px;height:8px}
.ticks li.long{text-align:justify;hyphens:auto;-webkit-hyphens:auto}
.price{position:absolute;left:29px;width:255px;height:21px;display:flex;gap:3px;font-size:9.6px}
.price-label{flex:0 0 166px;background:var(--chip);font-weight:500;color:var(--ink);padding-left:11px;display:flex;align-items:center}
.price-value{flex:1;background:var(--red);color:var(--white);font-weight:700;display:flex;align-items:center;justify-content:center}
.footnote{position:absolute;left:324px;top:703px;width:256px;font-size:9.6px;line-height:12.4px;text-align:justify}
.footer{position:absolute;left:0;top:765px;width:609px;height:52px}
.footer svg.band{position:absolute;inset:0}
.phone{position:absolute;left:28px;top:12px;display:flex;align-items:center;gap:7px;color:var(--white);font-family:"Open Sans",sans-serif;font-weight:700;font-size:17px}
.contacts{position:absolute;left:201px;top:15px;display:flex;align-items:center;gap:11px;font-family:"Open Sans",sans-serif;font-weight:600;font-size:9.5px;color:var(--white)}
.contact{display:flex;align-items:center;gap:5px}
.social{display:flex;gap:6px}
.social span{width:13px;height:13px;border-radius:50%;background:var(--white)}
</style>
</head>
<body>
<main class="flyer">
  <div class="hero-photo" role="img" aria-label="Photo of a smiling senior couple embracing in a bright home"></div>

  <div class="brand"><span class="brand-mark"></span><span class="brand-name">CORVANT SHIELD<br>INSURANCE</span></div>

  <h1 class="headline">Our <span class="accent">Plans Are</span><br>Based On Yours</h1>

  <div class="hero-rule"></div>

  <section class="col col-left">
    <p class="intro">Get the right Final Expense Insurance, Medicare Supplement Insurance or Mortgage Protection Insurance plan for your family's peace-of-mind!</p>

    <h2 class="heading" style="margin-top:24px">Final Expense Insurance</h2>
    <p class="para">Final Expense Insurance is a type of permanent life insurance where the death benefit is used to cover (but not limited to) medical costs, funeral costs and other end-of-life expenses. It is a budget friendly option with a death benefit of up to $40k.</p>

    <h2 class="heading" style="margin-top:18px">Benefits:</h2>
    <ul class="ticks">
      <li><svg viewBox="0 0 10 10"><rect x="0.8" y="1.5" width="7.5" height="7.5" fill="none" stroke="#d8222a" stroke-width="1.3"/><path d="M2.5 5l2 2 5-6" fill="none" stroke="#d8222a" stroke-width="1.5"/></svg>All plans we offer are state regulated</li>
      <li><svg viewBox="0 0 10 10"><rect x="0.8" y="1.5" width="7.5" height="7.5" fill="none" stroke="#d8222a" stroke-width="1.3"/><path d="M2.5 5l2 2 5-6" fill="none" stroke="#d8222a" stroke-width="1.5"/></svg>Relatively low monthly premiums</li>
      <li><svg viewBox="0 0 10 10"><rect x="0.8" y="1.5" width="7.5" height="7.5" fill="none" stroke="#d8222a" stroke-width="1.3"/><path d="M2.5 5l2 2 5-6" fill="none" stroke="#d8222a" stroke-width="1.5"/></svg>Premiums can never increase</li>
      <li><svg viewBox="0 0 10 10"><rect x="0.8" y="1.5" width="7.5" height="7.5" fill="none" stroke="#d8222a" stroke-width="1.3"/><path d="M2.5 5l2 2 5-6" fill="none" stroke="#d8222a" stroke-width="1.5"/></svg>Your policy can never be cancelled as long as you pay your premium</li>
      <li><svg viewBox="0 0 10 10"><rect x="0.8" y="1.5" width="7.5" height="7.5" fill="none" stroke="#d8222a" stroke-width="1.3"/><path d="M2.5 5l2 2 5-6" fill="none" stroke="#d8222a" stroke-width="1.5"/></svg>No medical exams</li>
      <li><svg viewBox="0 0 10 10"><rect x="0.8" y="1.5" width="7.5" height="7.5" fill="none" stroke="#d8222a" stroke-width="1.3"/><path d="M2.5 5l2 2 5-6" fill="none" stroke="#d8222a" stroke-width="1.5"/></svg>Guaranteed Death Benefit</li>
      <li class="long"><svg viewBox="0 0 10 10"><rect x="0.8" y="1.5" width="7.5" height="7.5" fill="none" stroke="#d8222a" stroke-width="1.3"/><path d="M2.5 5l2 2 5-6" fill="none" stroke="#d8222a" stroke-width="1.5"/></svg>Many policies we offer are Guaranteed Accep&shy;tance, "Day 1" coverage, have a child/grandchild rider and/or have an accelerated death benefit rider</li>
    </ul>
  </section>

  <div class="price" style="top:700px"><span class="price-label">Monthly premiums as low as</span><span class="price-value">$10</span></div>
  <div class="price" style="top:723px"><span class="price-label">Death Benefits as high as</span><span class="price-value">$40,000</span></div>

  <section class="col col-right">
    <h2 class="heading">We Also Specialize In:</h2>
    <ul class="ticks">
      <li><svg viewBox="0 0 10 10"><rect x="0.8" y="1.5" width="7.5" height="7.5" fill="none" stroke="#d8222a" stroke-width="1.3"/><path d="M2.5 5l2 2 5-6" fill="none" stroke="#d8222a" stroke-width="1.5"/></svg>Medicare Supplement Insurance (MediGap)</li>
      <li><svg viewBox="0 0 10 10"><rect x="0.8" y="1.5" width="7.5" height="7.5" fill="none" stroke="#d8222a" stroke-width="1.3"/><path d="M2.5 5l2 2 5-6" fill="none" stroke="#d8222a" stroke-width="1.5"/></svg>Annuities</li>
      <li><svg viewBox="0 0 10 10"><rect x="0.8" y="1.5" width="7.5" height="7.5" fill="none" stroke="#d8222a" stroke-width="1.3"/><path d="M2.5 5l2 2 5-6" fill="none" stroke="#d8222a" stroke-width="1.5"/></svg>Mortgage Protection Insurance</li>
    </ul>

    <h2 class="heading" style="margin-top:36px">Assessing Need</h2>
    <p class="para">Unforeseen events and a lack of the right kind of insurance can spell trouble quickly. Contact us today, to set up a free assessment time. We will analyze your insurance needs and get you and your family the right coverage quickly at a budget friendly price.</p>

    <h2 class="heading" style="margin-top:37px">Your Unique</h2>
    <p class="para">Everyone has different insurance needs.</p>
    <p class="para" style="margin-top:2px">Find out how we can give you the peace of mind knowing your family wont have a financial burden if something were to happen to you.</p>
    <p class="para" style="margin-top:12px">Find out how we can help find the right plan to keep your medical costs manageable.</p>
  </section>

  <p class="footnote">Based on an insured that is a 65 year old, non-smoking female that has no medical conditions with death benefit of $2k</p>

  <footer class="footer">
    <svg class="band" viewBox="0 0 609 52" preserveAspectRatio="none" aria-hidden="true">
      <rect x="0" y="0" width="609" height="52" fill="#d8222a"/>
      <polygon points="173,0 609,0 609,44 196,44" fill="#ffffff"/>
      <polygon points="177,1 609,1 609,43 199,43" fill="#262626"/>
    </svg>
    <div class="phone">
      <svg width="14" height="14" viewBox="0 0 24 24" aria-hidden="true"><path d="M6.6 10.8a15.1 15.1 0 0 0 6.6 6.6l2.2-2.2a1 1 0 0 1 1-.25 11.4 11.4 0 0 0 3.6.57 1 1 0 0 1 1 1V20a1 1 0 0 1-1 1A17 17 0 0 1 3 4a1 1 0 0 1 1-1h3.5a1 1 0 0 1 1 1c0 1.25.2 2.45.57 3.57a1 1 0 0 1-.25 1z" fill="#ffffff"/></svg>
      (208)555.0147
    </div>
    <div class="contacts">
      <span class="contact"><svg width="10" height="8" viewBox="0 0 10 8" aria-hidden="true"><rect x="0.5" y="0.5" width="9" height="7" fill="none" stroke="#d8222a"/><path d="M0.5 0.5l4.5 4 4.5-4" fill="none" stroke="#d8222a"/></svg>tkelwer@corvantshield.com</span>
      <span class="contact"><svg width="9" height="9" viewBox="0 0 10 10" aria-hidden="true"><circle cx="5" cy="5" r="4.3" fill="none" stroke="#d8222a"/><ellipse cx="5" cy="5" rx="2" ry="4.3" fill="none" stroke="#d8222a"/><path d="M0.7 5h8.6" stroke="#d8222a"/></svg>www.corvantshield.com</span>
      <span class="social" aria-label="Social media"><span></span><span></span></span>
    </div>
  </footer>
</main>
</body>
</html>
```